Design material for Lumora Event

We need a design of POSM for Lumora Event
1. Content:
- The Lumora Event 3rd
- Singapore 28.10.2018
- A placeholder for insert logo of sponsors (limit 10 logo)
2. POSM:
- Backdrop: 5,5m and 2,6m
- Banner: 4m and 0,5m
- Standee: 0,8m and 2m
- Cover: A4 size
3. Style:
We need style simply because we are a hospital.
Main color: light blue and a little of green (if can)

Hope to see your design soon!

Font styles to use
Sans Serif

Colors
0792cd
85cae6
86cfc6
33b8a4
33a6d7

```html
<!DOCTYPE html>
<html lang="en">
<head>
<meta charset="utf-8">
<title>Lumora Event 2018 Singapore – Banner</title>
<link href="https://fonts.googleapis.com/css2?family=Quicksand:wght@600;700&family=Montserrat:wght@600;700&display=swap" rel="stylesheet">
<style>
  :root {
    --navy: #125a86;
    --blue: #0792cd;
    --sky: #85cae6;
    --mint: #86cfc6;
    --teal: #33b8a4;
    --azure: #33a6d7;
    --white: #ffffff;
    --lattice: #e6e8ea;
    --sponsor: #b9bec4;
  }
  * { margin: 0; padding: 0; box-sizing: border-box; }
  html, body { width: 1200px; height: 151px; overflow: hidden; background: var(--white); }
  .banner { position: relative; width: 1200px; height: 151px; overflow: hidden; background: var(--white); font-family: "Quicksand", sans-serif; }
  .lattice-texture {
    position: absolute; left: 0; top: 0; width: 560px; height: 151px;
    background: linear-gradient(100deg, var(--lattice) 0%, #f3f4f5 45%, rgba(255,255,255,0) 100%);
  }
  .edition-tab { position: absolute; left: 0; top: 0; width: 140px; height: 151px; }
  .edition {
    position: absolute; left: 22px; top: 30px; color: var(--white);
    font-family: "Montserrat", sans-serif; font-weight: 700; font-size: 70px; line-height: 1;
  }
  .edition sup { font-size: 20px; font-weight: 600; vertical-align: top; position: relative; top: 2px; margin-left: 2px; }
  .event-title {
    position: absolute; left: 130px; top: 48px; color: var(--navy);
    font-weight: 700; font-size: 54px; line-height: 1; letter-spacing: -0.5px;
  }
  .event-site {
    position: absolute; left: 336px; top: 116px; color: var(--teal);
    font-weight: 700; font-size: 18px; line-height: 1;
  }
  .emblem { position: absolute; left: 555px; top: 0; width: 300px; height: 151px; }
  .year-badge { position: absolute; left: 738px; top: 24px; width: 104px; height: 104px; }
  .year {
    position: absolute; left: 738px; top: 60px; width: 104px; text-align: center;
    color: var(--white); font-family: "Montserrat", sans-serif; font-weight: 700; font-size: 22px; line-height: 32px;
  }
  .city {
    position: absolute; left: 866px; top: 54px; color: var(--teal);
    font-family: "Montserrat", sans-serif; font-weight: 700; font-size: 28px; letter-spacing: 9px; line-height: 1;
  }
  .sponsors { position: absolute; left: 800px; top: 110px; display: flex; gap: 8px; align-items: center; }
  .sponsor { width: 32px; height: 16px; background: var(--sponsor); border-radius: 2px; }
  .sponsor.round { width: 16px; height: 16px; border-radius: 50%; }
</style>
</head>
<body>
<div class="banner">
  <div class="lattice-texture" role="img" aria-label="Soft grey geometric lattice texture"></div>

  <svg class="edition-tab" viewBox="0 0 140 151" aria-hidden="true">
    <polygon points="0,0 108,0 138,30 100,151 0,151" fill="var(--teal)"/>
  </svg>
  <div class="edition">3<sup>rd</sup></div>

  <h1 class="event-title">Lumora Event</h1>
  <div class="event-site">LumoraEvent.com</div>

  <svg class="emblem" viewBox="0 0 300 151" aria-hidden="false">
    <defs>
      <linearGradient id="cityTone" x1="0" y1="0" x2="0" y2="1">
        <stop offset="0" stop-color="#7fa9c9"/>
        <stop offset="0.5" stop-color="#d9c9a8"/>
        <stop offset="1" stop-color="#6f8ea0"/>
      </linearGradient>
    </defs>
    <polygon points="103,-12 160,-12 188,12 130,12" fill="var(--mint)" opacity="0.8"/>
    <polygon points="58,75 103,30 113,40 78,75 113,110 103,120" fill="var(--navy)"/>
    <polygon points="103,8 170,75 103,142 36,75" fill="none" stroke="var(--mint)" stroke-width="2"/>
    <polygon points="130,30 178,78 130,126 82,78" fill="none" stroke="var(--teal)" stroke-width="1.5"/>
    <polygon points="150,118 178,146 150,174 122,146" fill="var(--sky)"/>
    <polygon points="103,14 164,75 103,136 42,75" fill="url(#cityTone)" role="img" aria-label="Photo of the Singapore skyline at sunset over the bay"/>
  </svg>

  <svg class="year-badge" viewBox="0 0 104 104" aria-hidden="true">
    <polygon points="52,0 104,52 52,104 0,52" fill="var(--teal)"/>
    <circle cx="52" cy="52" r="30" fill="none" stroke="var(--white)" stroke-width="2"/>
  </svg>
  <div class="year">2018</div>

  <div class="city">SINGAPORE</div>

  <div class="sponsors" aria-label="Sponsor placeholders">
    <span class="sponsor"></span>
    <span class="sponsor round"></span>
    <span class="sponsor round"></span>
    <span class="sponsor"></span>
    <span class="sponsor round"></span>
    <span class="sponsor"></span>
    <span class="sponsor"></span>
    <span class="sponsor round"></span>
    <span class="sponsor"></span>
    <span class="sponsor"></span>
  </div>
</div>
</body>
</html>
```